Security and Technology Website - Bold and Confident, Something Unexpected

Maple Wren Systems is launching its first website and we need a great design to bring our brand to life and generate DTC and B2B leads.

We have a good logo, but I am struggling with the creative vision to bring it all together. While our industry is Alarm Systems and Technology, we want to create a site that is more friendly and less 'typical' than your standard IT sites.

It Must:
1. Appeal to both men and women. The logo is a bit masculine, so the colors and icons must soften this.
2. Feel modern - we need to convey that we we use the latest technology.
3. Feel a bit high-end. We are not a budget solution.
4. Have a distinct iconography and photo treatment.
5. Feel layered - not just a series of stacked horizontal modules.

It Should Not:
1. Feel like your typical IT website.

Here are resources to get you started!
• Staging Site:
https://maple-wren-systems.shopfrontdemo.example/
Password: Piper

•Brand Guide: https://www.layoutboard.example/design/QKRmWpLcT4V/hNbq8Yf2-ZsKeRtDw7xp-QE/edit?utm_content=QKRmWpLcT4V&utm_campaign=designshare&utm_medium=link2&utm_source=sharebutton

• Logo and Fonts and Photos: :https://files.cloudlocker.example/folders/7HtPqWmZc3Kd9RbLx2VnYs8FgJe4UoAiT?usp=sharing

• Design Inspiration (don't feel limited by this): https://www.layoutboard.example/design/QKTnHsVbWe8/p7MfRz31xYqLcKdTu9GNBw/edit?utm_content=QKTnHsVbWe8&utm_campaign=designshare&utm_medium=link2&utm_source=sharebutton

______________

The winner will be asked to provide design files and finished PNGs of the overall design file, backgrounds, photo treatments/frames, and icons.

The winner will likely be engaged for a phase 2 to build out a product page.

Industry/Entity Type

Alarm Systems, Home Theatres, and Commercial IT Networking

Number of Pages Required

1 page

Font styles to use
Sans Serif

Colors
0054AA
0677BA
7BADD7
CADEEF
E8F1F8
0094D4
00A9DD
6FCCEA
C7EBF8
E9F6FB
EB3D1F
EC4F4E
F09395
F8D3D4
FCEDEE

Requirements
Must have
• 1. Appeal to both men and women. The logo is a bit masculine, so the colors and icons must soften this. 2. Feel modern - we need to convey that we we use the latest technology. 3. Feel a bit high-end. We are not a budget solution. 4. Have a distinct iconography and photo treatment. 5. Feel layered - not just a series of stacked horizontal modules.
Should not have
• 1. Should not feel like just another IT website.

```html
<!DOCTYPE html>
<html lang="en">
<head>
<meta charset="utf-8">
<title>Maple Wren Systems</title>
<link href="https://fonts.googleapis.com/css2?family=Audiowide&family=Outfit:wght@400;500;600;700&display=swap" rel="stylesheet">
<style>
:root{
  --blue:#1a86f0;
  --blue-deep:#0054aa;
  --blue-band:#0a5fd6;
  --red:#d4060f;
  --red-deep:#a8060c;
  --ink:#111418;
  --muted:#555b63;
  --dark:#0e1013;
  --white:#ffffff;
  --pale:#e9f6fb;
}
html,body{margin:0;padding:0;width:1200px;height:3846px;overflow:hidden;background:#fff;}
.page{position:relative;width:1200px;height:3846px;overflow:hidden;font-family:"Outfit",sans-serif;color:var(--ink);}
.abs{position:absolute;}
.display{font-family:"Audiowide",sans-serif;}
.center{text-align:center;}
/* hero */
.hero-photo{left:0;top:0;width:1200px;height:700px;background:linear-gradient(115deg,#05080d 0%,#0c1826 40%,#183c5e 70%,#0a1420 100%);}
.hero-shape{left:0;top:520px;width:1200px;height:190px;}
.brand{left:116px;top:60px;color:#fff;font-family:"Outfit",sans-serif;font-weight:700;font-size:30px;line-height:36px;letter-spacing:1px;display:flex;align-items:center;gap:12px;}
.brand .mark{width:22px;height:22px;background:#fff;}
.nav{top:75px;left:461px;display:flex;gap:30px;color:#fff;font-size:14px;font-weight:500;}
.nav span.on{border-bottom:2px solid #fff;padding-bottom:3px;}
.top-icons{top:30px;left:925px;display:flex;gap:16px;align-items:center;}
.cart{left:995px;top:23px;width:102px;height:36px;background:var(--blue);border-radius:4px;color:#fff;font-size:13px;display:flex;align-items:center;justify-content:center;gap:6px;}
.tagline{left:110px;top:234px;color:#fff;font-weight:600;font-size:28px;letter-spacing:.5px;}
.hero-title{left:108px;top:276px;color:#fff;font-size:60px;line-height:68px;}
.hero-lede{left:110px;top:410px;color:#fff;font-size:19px;line-height:30px;width:480px;}
.btn-red{left:110px;top:484px;width:138px;height:40px;background:var(--red);color:#fff;border-radius:5px;font-weight:600;font-size:15px;display:flex;align-items:center;justify-content:center;}
/* section heads */
.eyebrow{left:0;width:1200px;text-align:center;color:var(--red);font-size:21px;font-weight:500;letter-spacing:.5px;}
.h2{left:0;width:1200px;text-align:center;font-size:39px;color:var(--ink);}
/* feature cards */
.fcard{top:907px;width:306px;height:369px;background:#fff;border-radius:14px;box-shadow:0 6px 30px rgba(20,40,80,.09);}
.fcard.alt{background:linear-gradient(180deg,#e2f1fc 0%,#fff 100%);}
.ring{top:854px;width:128px;height:128px;border-radius:50%;display:flex;align-items:center;justify-content:center;box-shadow:0 8px 20px rgba(0,0,0,.18);}
.ring.red{background:radial-gradient(circle,#e01018 50%,#b4050b 51%);}
.ring.blue{background:radial-gradient(circle,#1d7ff0 50%,#0a56c2 51%);}
.fcard h3{position:absolute;top:96px;left:0;width:100%;margin:0;text-align:center;font-size:16px;font-weight:700;letter-spacing:.5px;}
.fcard p{position:absolute;top:128px;left:20px;right:20px;margin:0;text-align:center;font-size:12px;line-height:27px;color:var(--muted);}
.fcard ul{position:absolute;top:196px;left:54px;margin:0;padding:0;list-style:none;font-size:12px;color:var(--muted);}
.fcard li{height:28px;display:flex;align-items:center;gap:10px;}
.btn-blue{background:var(--blue);color:#fff;border-radius:5px;font-size:14px;font-weight:500;display:flex;align-items:center;justify-content:center;box-shadow:0 6px 14px rgba(26,134,240,.3);}
.fcard .btn-blue{position:absolute;left:54px;top:294px;width:199px;height:41px;}
/* about */
.portrait{left:112px;top:1361px;width:446px;height:412px;border-radius:30px 30px 30px 30px;background:linear-gradient(160deg,#cdeef7 0%,#bfe6f3 55%,#1f2a3d 100%);}
.about-copy{left:620px;width:470px;text-align:center;}
/* blue band */
.band{left:0;top:1877px;width:1200px;height:493px;background:radial-gradient(ellipse at 50% 30%,#2a7df2 0%,#0b5bd8 55%,#0848b4 100%);}
.scard{top:2054px;width:236px;height:247px;background:#fff;border-radius:12px;text-align:center;}
.scard.alt{background:linear-gradient(135deg,#fbe0e2 0%,#fff 30%,#fff 70%,#f3b4b8 100%);border:3px solid #fff;box-sizing:border-box;}
.scard .ico{width:56px;height:56px;border-radius:50%;background:var(--red);margin:31px auto 0;display:flex;align-items:center;justify-content:center;}
.scard h4{margin:20px 0 0;font-size:17px;font-weight:700;line-height:24px;letter-spacing:.5px;}
.scard p{margin:10px 24px 0;font-size:11.5px;line-height:21px;color:var(--muted);}
/* steps */
.step{top:2537px;width:309px;height:66px;}
.step-label{position:absolute;left:38px;top:0;height:66px;display:flex;align-items:center;color:#fff;font-size:23px;font-family:"Audiowide",sans-serif;}
.step-title{top:2619px;font-size:19px;font-weight:600;}
.step-text{top:2658px;width:300px;font-size:13px;line-height:25px;color:var(--muted);}
/* testimonial */
.quote-box{left:112px;top:2816px;width:976px;height:352px;border-radius:24px;background:radial-gradient(ellipse at 50% 50%,#c1060d 0%,#a6040a 100%);}
.avatar{left:185px;top:2955px;width:72px;height:72px;border-radius:50%;background:linear-gradient(160deg,#d7e6f0,#5a6b80);border:3px solid #fff;box-sizing:border-box;}
/* partners */
.partner{top:3213px;width:221px;height:145px;background:#fff;box-shadow:0 4px 20px rgba(0,0,0,.06);display:flex;align-items:center;justify-content:center;}
/* footer */
.footer{left:0;top:3403px;width:1200px;height:443px;background:var(--dark);}
.fnav{top:3465px;left:0;width:1200px;display:flex;justify-content:center;gap:24px;color:#fff;font-size:14px;font-weight:500;}
.fhead{top:3584px;color:#fff;font-size:19px;}
.fline{color:#fff;font-size:13px;display:flex;align-items:center;gap:16px;}
</style>
</head>
<body>
<div class="page">

  <!-- HERO -->
  <div class="abs hero-photo" role="img" aria-label="Team of technicians gathered around a monitor in a dark room with data overlays"></div>
  <svg class="abs hero-shape" viewBox="0 0 1200 190" preserveAspectRatio="none">
    <path d="M0 20 Q300 90 600 178 Q900 90 1200 20 L1200 190 L0 190 Z" fill="#0b5fe0"/>
    <path d="M0 20 Q300 70 600 120 Q900 70 1200 20 L1200 190 L0 190 Z" fill="#fff"/>
    <path d="M160 45 Q380 110 600 178 Q820 110 1040 45 Q820 90 600 150 Q380 90 160 45 Z" fill="#1a86f0"/>
    <path d="M170 58 Q400 118 600 178 Q800 118 1030 58 Q800 132 600 178 Q400 132 170 58Z" fill="#0b5fe0"/>
    <path d="M0 20 Q300 70 600 120 Q900 70 1200 20 L1200 190 L0 190 Z" fill="#fff" transform="translate(0,26)"/>
  </svg>

  <div class="abs brand"><span class="mark"></span>MAPLE WREN<br>SYSTEMS</div>
  <div class="abs nav"><span class="on">HOME</span><span>Electronic Security</span><span>Audio + Video</span><span>Networking + Communication</span><span>Cabling</span></div>
  <div class="abs top-icons">
    <svg width="14" height="14" viewBox="0 0 14 14"><circle cx="7" cy="4" r="3.3" fill="#fff"/><path d="M1 14c0-4 3-6 6-6s6 2 6 6z" fill="#fff"/></svg>
    <svg width="16" height="14" viewBox="0 0 16 14"><path d="M8 13 1.8 7A3.7 3.7 0 0 1 8 2.5 3.7 3.7 0 0 1 14.2 7z" fill="none" stroke="#fff" stroke-width="1.6"/></svg>
  </div>
  <div class="abs cart"><svg width="13" height="12" viewBox="0 0 13 12"><path d="M0 1h2.5l2 7h6.5l1.5-5H4" fill="none" stroke="#fff" stroke-width="1.5"/><circle cx="5" cy="10.5" r="1.2" fill="#fff"/><circle cx="10" cy="10.5" r="1.2" fill="#fff"/></svg>Cart (0)</div>

  <div class="abs tagline">SAFER. SMARTER. FASTER.</div>
  <div class="abs hero-title display">MAPLE WREN<br>SYSTEMS</div>
  <div class="abs hero-lede">Protect your people, assets, and information from whatever comes.</div>
  <div class="abs btn-red">Get Started</div>

  <!-- FEATURES -->
  <div class="abs eyebrow" style="top:748px;">FEATURES</div>
  <div class="abs h2 display" style="top:780px;">WHY CHOOSE US</div>

  <div class="abs fcard" style="left:110px;">
    <h3>AFFORDABLE SECURITY</h3>
    <p>We denounce with righteous indignation<br>and dislike men who are so beg</p>
    <ul>
      <li><svg width="11" height="9" viewBox="0 0 11 9"><path d="M1 4.5 4 7.5 10 1" fill="none" stroke="#555b63" stroke-width="2"/></svg>For Homes</li>
      <li><svg width="11" height="9" viewBox="0 0 11 9"><path d="M1 4.5 4 7.5 10 1" fill="none" stroke="#555b63" stroke-width="2"/></svg>For Businesses</li>
    </ul>
    <div class="btn-blue">View All Details</div>
  </div>
  <div class="abs fcard alt" style="left:446px;">
    <h3>ENVIABLE ENTERTAINMENT</h3>
    <p>We denounce with righteous indignation<br>and dislike men who are so beg</p>
    <ul>
      <li><svg width="11" height="9" viewBox="0 0 11 9"><path d="M1 4.5 4 7.5 10 1" fill="none" stroke="#555b63" stroke-width="2"/></svg>Home Theatres</li>
      <li><svg width="11" height="9" viewBox="0 0 11 9"><path d="M1 4.5 4 7.5 10 1" fill="none" stroke="#555b63" stroke-width="2"/></svg>Smart Homes</li>
      <li><svg width="11" height="9" viewBox="0 0 11 9"><path d="M1 4.5 4 7.5 10 1" fill="none" stroke="#555b63" stroke-width="2"/></svg>Whole Home A/V</li>
    </ul>
    <div class="btn-blue">View All Details</div>
  </div>
  <div class="abs fcard" style="left:784px;">
    <h3>CONNECTED BUSINESSES</h3>
    <p>We denounce with righteous indignation<br>and dislike men who are so beg</p>
    <ul>
      <li><svg width="11" height="9" viewBox="0 0 11 9"><path d="M1 4.5 4 7.5 10 1" fill="none" stroke="#555b63" stroke-width="2"/></svg>Conference Systems</li>
      <li><svg width="11" height="9" viewBox="0 0 11 9"><path d="M1 4.5 4 7.5 10 1" fill="none" stroke="#555b63" stroke-width="2"/></svg>Phones</li>
      <li><svg width="11" height="9" viewBox="0 0 11 9"><path d="M1 4.5 4 7.5 10 1" fill="none" stroke="#555b63" stroke-width="2"/></svg>Networking and Wifi</li>
    </ul>
    <div class="btn-blue">View All Details</div>
  </div>

  <div class="abs ring red" style="left:200px;">
    <svg width="44" height="50" viewBox="0 0 44 50"><path d="M22 2 40 9v14c0 12-8 21-18 25C12 44 4 35 4 23V9z" fill="#fff"/><path d="M14 25l6 6 11-12" fill="none" stroke="#d4060f" stroke-width="4"/></svg>
  </div>
  <div class="abs ring blue" style="left:537px;">
    <svg width="48" height="44" viewBox="0 0 48 44"><rect x="4" y="14" width="12" height="28" rx="2" fill="#fff"/><rect x="18" y="10" width="12" height="32" rx="2" fill="#fff"/><rect x="32" y="14" width="12" height="28" rx="2" fill="#fff"/><circle cx="24" cy="30" r="4" fill="#0a56c2"/><path d="M16 6a12 12 0 0 1 16 0M19 2a18 18 0 0 0 0 0" fill="none" stroke="#fff" stroke-width="2.5"/></svg>
  </div>
  <div class="abs ring red" style="left:873px;">
    <svg width="50" height="50" viewBox="0 0 50 50"><g fill="#fff"><circle cx="25" cy="8" r="6"/><circle cx="8" cy="25" r="6"/><circle cx="42" cy="25" r="6"/><circle cx="25" cy="42" r="6"/><circle cx="25" cy="25" r="4"/></g><path d="M25 8 8 25 25 42 42 25Z" fill="none" stroke="#fff" stroke-width="2"/></svg>
  </div>

  <!-- ABOUT -->
  <div class="abs portrait" role="img" aria-label="Portrait of the company founder in a suit and bow tie against a pale blue backdrop"></div>
  <div class="abs about-copy" style="top:1385px;color:var(--red);font-size:21px;font-weight:500;">WHO WE ARE</div>
  <div class="abs about-copy display" style="top:1418px;font-size:39px;">HOW CAN WE HELP</div>
  <div class="abs about-copy" style="top:1478px;color:var(--blue);font-size:18px;font-weight:500;line-height:32px;">I founded Maple Wren Systems to bring together<br>technology and honest, reliable service.</div>
  <div class="abs about-copy" style="top:1549px;color:#3a3f45;font-size:17px;line-height:32.5px;">I'm proud to call Tennessee home and even prouder to help keep its homes and businesses secure. Whether it's protecting or elevating your space, my goal is to make technology work for you.</div>
  <div class="abs btn-blue" style="left:745px;top:1701px;width:218px;height:45px;font-size:15px;">View More Details</div>

  <!-- BLUE BAND -->
  <div class="abs band" role="img" aria-label="Glowing blue network mesh over a night city"></div>
  <div class="abs eyebrow" style="top:1942px;color:#e0101a;">JOIN WITH US</div>
  <div class="abs h2 display" style="top:1977px;color:#fff;">CONNECT + PROTECT YOUR WORLD</div>

  <div class="abs scard" style="left:97px;">
    <div class="ico"><svg width="30" height="22" viewBox="0 0 30 22"><circle cx="15" cy="11" r="3.5" fill="#fff"/><path d="M9 5a9 9 0 0 0 0 12M21 5a9 9 0 0 1 0 12M5 2a14 14 0 0 0 0 18M25 2a14 14 0 0 1 0 18" fill="none" stroke="#fff" stroke-width="2"/></svg></div>
    <h4>ENTRY &amp; MOTION<br>SENSORS</h4>
    <p>Ut enim ad minima veniam, quis nostrum exercitationem ullam corporis suscipit</p>
  </div>
  <div class="abs scard alt" style="left:354px;">
    <div class="ico" style="margin-top:28px;"><svg width="28" height="18" viewBox="0 0 28 18"><rect x="1" y="2" width="18" height="14" rx="3" fill="#fff"/><path d="M20 9l7-5v10z" fill="#fff"/></svg></div>
    <h4>VIDEO<br>DOORBELLS</h4>
    <p>Ut enim ad minima veniam, quis nostrum exercitationem ullam corporis suscipit</p>
  </div>
  <div class="abs scard" style="left:610px;">
    <div class="ico"><svg width="30" height="26" viewBox="0 0 30 26"><path d="M3 6l20 7-3 6L2 12z" fill="#fff"/><path d="M22 15l5 2v6h-3v-4l-3-1" fill="#fff"/></svg></div>
    <h4>OUR SECURITY<br>CAMERAS</h4>
    <p>Ut enim ad minima veniam, quis nostrum exercitationem ullam corporis suscipit</p>
  </div>
  <div class="abs scard" style="left:867px;">
    <div class="ico"><svg width="22" height="28" viewBox="0 0 22 28"><path d="M11 1c2 6 10 9 10 17a10 10 0 0 1-20 0c0-5 4-7 5-11 1 3 2 4 3 5 1-4 2-7 2-11z" fill="#fff"/><circle cx="11" cy="20" r="4" fill="#d4060f"/></svg></div>
    <h4>FIRE &amp; CARBON<br>MONOXIDE</h4>
    <p>Ut enim ad minima veniam, quis nostrum exercitationem ullam corporis suscipit</p>
  </div>

  <!-- HOW IT WORKS -->
  <div class="abs eyebrow" style="top:2433px;">A SAFER HOME OR BUSINESS IS AS EASY AS 1-2-3</div>
  <div class="abs h2 display" style="top:2467px;">HOW IT WORKS</div>

  <div class="abs step" style="left:112px;">
    <svg width="309" height="66" viewBox="0 0 309 66"><path d="M0 0H296L309 33 296 66H0L12 33Z" fill="#1a86f0"/></svg>
    <div class="step-label">STEP 01</div>
  </div>
  <div class="abs step" style="left:446px;">
    <svg width="309" height="66" viewBox="0 0 309 66"><path d="M0 0H296L309 33 296 66H0L12 33Z" fill="#c7060d"/></svg>
    <div class="step-label">STEP 02</div>
  </div>
  <div class="abs step" style="left:779px;">
    <svg width="309" height="66" viewBox="0 0 309 66"><path d="M0 0H296L309 33 296 66H0L12 33Z" fill="#1a86f0"/></svg>
    <div class="step-label">STEP 03</div>
  </div>

  <div class="abs step-title" style="left:112px;">Build an Instant Quote</div>
  <div class="abs step-title" style="left:446px;">Schedule Installation</div>
  <div class="abs step-title" style="left:779px;">Stay Secure 24/7</div>
  <div class="abs step-text" style="left:112px;">Our live-estimate builder will guide you through a few questions to help us understand your needs.</div>
  <div class="abs step-text" style="left:447px;">Our trained techs are efficient and friendly. Southern-born and raised (and one mid-westerner), we will respect your home and your schedule.</div>
  <div class="abs step-text" style="left:780px;">Monitor your home through the app, receive instant alerts, and rely on professional monitoring services for emergencies.</div>

  <!-- TESTIMONIAL -->
  <div class="abs quote-box"></div>
  <div class="abs avatar" role="img" aria-label="Customer portrait"></div>
  <div class="abs" style="left:279px;top:2969px;color:#fff;font-family:'Audiowide',sans-serif;font-size:14px;">NORA T</div>
  <div class="abs" style="left:279px;top:2994px;color:#fff;font-size:13px;">Cedar Bluff, TN</div>
  <div class="abs" style="left:515px;top:2870px;width:1px;height:245px;background:rgba(255,255,255,.6);"></div>
  <div class="abs" style="left:493px;top:2970px;width:44px;height:44px;border-radius:50%;background:#fff;display:flex;align-items:center;justify-content:center;">
    <svg width="18" height="14" viewBox="0 0 18 14"><path d="M0 14V8Q0 2 6 0v3Q3 4 3 7h4v7zM10 14V8q0-6 6-8v3q-3 1-3 4h4v7z" fill="#c1060d"/></svg>
  </div>
  <div class="abs" style="left:591px;top:2910px;width:420px;color:#fff;font-size:12px;line-height:26px;">Fantastic service!! Used Brightline and HomeCove in the past, and their customer service does not compare to Maple Wren! Installation and set up went smoothly!! It's so convenient to use the apps remotely for the cameras, and arming or unarming the alarm. I'd rate them more than 5 stars if I was able to!</div>

  <!-- PARTNERS -->
  <div class="abs partner" style="left:45px;"><div style="width:150px;height:44px;background:#1b1b1b;border-radius:4px;"></div></div>
  <div class="abs partner" style="left:267px;"><div style="width:150px;height:34px;background:#222;border-radius:17px;"></div></div>
  <div class="abs partner" style="left:490px;"><div style="width:150px;height:34px;background:#6d8fc6;border-radius:4px;"></div></div>
  <div class="abs partner" style="left:712px;"><div style="width:180px;height:40px;background:#3f9b3a;border-radius:4px;"></div></div>
  <div class="abs partner" style="left:934px;"><div style="width:64px;height:64px;background:#e8571f;border-radius:50%;"></div></div>

  <!-- FOOTER -->
  <div class="abs footer"></div>
  <div class="abs fnav"><span>Home</span><span>|</span><span>Electronic Security</span><span>|</span><span>Audio + Video</span><span>|</span><span>Networking + Communication</span><span>|</span><span>Cabling</span></div>
  <div class="abs" style="left:112px;top:3528px;width:976px;height:1px;background:#2a2d33;"></div>

  <div class="abs fhead display" style="left:110px;">CONTACT US</div>
  <div class="abs fline" style="left:112px;top:3630px;"><svg width="11" height="15" viewBox="0 0 11 15"><path d="M5.5 0A5.5 5.5 0 0 0 0 5.5C0 10 5.5 15 5.5 15S11 10 11 5.5A5.5 5.5 0 0 0 5.5 0z" fill="#fff"/><circle cx="5.5" cy="5.5" r="2" fill="#0e1013"/></svg>240 Harbor Ridge Rd. Suite 3-112</div>
  <div class="abs fline" style="left:143px;top:3663px;">Fairview Hollow, TN 37000</div>
  <div class="abs fline" style="left:112px;top:3696px;"><svg width="12" height="12" viewBox="0 0 12 12"><path d="M2.5 0 5 3 3.5 4.8a8 8 0 0 0 3.7 3.7L9 7l3 2.5-1.7 2.3C5 11.5.5 7 .2 1.7z" fill="#fff"/></svg>615.555.0142 (Contact)</div>
  <div class="abs fline" style="left:112px;top:3729px;"><svg width="12" height="9" viewBox="0 0 12 9"><rect width="12" height="9" rx="1" fill="#fff"/><path d="M0 1l6 4 6-4" fill="none" stroke="#0e1013" stroke-width="1.2"/></svg>info@maplewren.example (Email)</div>

  <div class="abs" style="left:478px;top:3620px;width:249px;text-align:center;color:#1a86f0;font-weight:700;font-size:32px;line-height:40px;display:flex;flex-direction:column;align-items:center;gap:10px;">
    <span style="width:20px;height:20px;background:#1a86f0;"></span>
    <span>MAPLE WREN<br>SYSTEMS</span>
  </div>

  <div class="abs fhead display" style="right:112px;">ABOUT US</div>
  <div class="abs" style="right:112px;top:3627px;width:290px;text-align:right;color:#fff;font-size:12.5px;line-height:28.5px;">Our team is always on guard. With always-on protection, we'll notify you of any suspicious activity. In emergencies, we'll monitor your local police, fire, or EMS.</div>

  <div class="abs" style="left:0;top:3813px;width:1200px;text-align:center;color:#fff;font-size:12px;">(C) Copyright 2024 | All Rights Reserved</div>
</div>
</body>
</html>
```